Young, dynamic furniture company needs a new business card design

We require a new business card design for our modern furniture company which supplies furniture and appliances to the property and development market.
Oakridge Interiors has become one of the leading furniture & appliance suppliers to the property market withing London. With over 10 years experience, we have increased our business to supply not only private landlords and managing agents, but also property developers, housing associations and local councils.
We offer not only a complete range of furniture which includes beds, wardrobes, dining sets and sofas, but also a high quality, full delivery and assembly service to help you with all our furnishing needs.

Target Market(s)

Private landlords, estate agents, letting agents, property management companies

Industry/Entity Type

Business

Contact Information for Business Card

Name,
Title,
Address,
Mobile,
Telephone,
Fax, Website, email address

Font styles to use
Sans Serif

Colors
3176b5
0555a3
85abd2
cfdeed

Requirements
Must have
• All the above information for each of our staff, along with our logo

```html
<!DOCTYPE html>
<html lang="en">
<head>
<meta charset="utf-8">
<title>Oakridge Interiors – Business Card</title>
<link rel="stylesheet" href="https://fonts.googleapis.com/css2?family=Lato:wght@400;700&display=swap">
<style>
  :root {
    --blue-mid: #3176b5;
    --blue-deep: #0555a3;
    --blue-light: #85abd2;
    --blue-pale: #cfdeed;
    --ink: #111111;
    --paper: #ffffff;
    --stage: #e6e8eb;
  }
  * { box-sizing: border-box; margin: 0; padding: 0; }
  html, body { width: 1200px; height: 900px; overflow: hidden; }
  body {
    background: var(--stage);
    font-family: "Lato", sans-serif;
    position: relative;
  }
  .card {
    position: absolute;
    left: 250px;
    width: 700px;
    height: 400px;
    overflow: hidden;
    box-shadow: 0 6px 18px rgba(0,0,0,0.18);
  }
  /* Back side */
  .card-back {
    top: 30px;
    background: var(--blue-deep);
    color: var(--paper);
    display: flex;
    flex-direction: column;
    align-items: center;
    justify-content: center;
    text-align: center;
  }
  .brand {
    display: flex;
    align-items: center;
    gap: 12px;
  }
  .brand-mark {
    width: 22px;
    height: 22px;
    background: var(--paper);
  }
  .brand-name {
    font-size: 34px;
    font-weight: 400;
    letter-spacing: 1px;
    text-transform: uppercase;
  }
  .brand-tagline {
    font-size: 15px;
    letter-spacing: 1.5px;
    text-transform: uppercase;
    margin-top: 6px;
  }
  .card-back .web {
    font-size: 19px;
    letter-spacing: 3px;
    margin-top: 30px;
  }
  /* Front side */
  .card-front {
    top: 470px;
    background: var(--paper);
    color: var(--ink);
  }
  .card-front .faint-name {
    position: absolute;
    left: 30px;
    top: 10px;
    font-size: 62px;
    font-weight: 700;
    color: #f3f4f6;
    text-transform: uppercase;
    white-space: nowrap;
  }
  .person {
    position: absolute;
    left: 40px;
    top: 52px;
  }
  .person-name {
    font-size: 30px;
    color: var(--blue-mid);
    font-weight: 400;
  }
  .person-title {
    font-size: 17px;
    margin-top: 2px;
  }
  .card-front .brand {
    position: absolute;
    right: 40px;
    top: 50px;
    flex-direction: column;
    align-items: flex-start;
    gap: 2px;
  }
  .card-front .brand-row { display: flex; align-items: center; gap: 10px; }
  .card-front .brand-mark { background: var(--blue-mid); width: 20px; height: 20px; }
  .card-front .brand-name { font-size: 28px; color: var(--ink); }
  .card-front .brand-tagline { font-size: 13px; margin-top: 0; padding-left: 30px; }
  .divider {
    position: absolute;
    left: 40px;
    right: 40px;
    top: 140px;
    height: 2px;
    background: var(--ink);
  }
  .contacts {
    position: absolute;
    left: 40px;
    top: 160px;
    list-style: none;
    font-size: 19px;
    line-height: 28px;
  }
  .contacts li { display: flex; align-items: center; gap: 12px; }
  .contacts svg { width: 16px; height: 16px; flex: none; }
  .address {
    position: absolute;
    right: 40px;
    top: 270px;
    text-align: right;
    font-size: 23px;
    line-height: 30px;
  }
  .edge-band {
    position: absolute;
    left: 0;
    bottom: 0;
    width: 700px;
    height: 30px;
  }
</style>
</head>
<body>

<section class="card card-back">
  <div class="brand">
    <span class="brand-mark"></span>
    <span class="brand-name">Oakridge Interiors</span>
  </div>
  <p class="brand-tagline">Trade Furniture Solutions</p>
  <p class="web">www.trade.oakridge.co.uk</p>
</section>

<section class="card card-front">
  <span class="faint-name" aria-hidden="true">Oakridge</span>

  <div class="person">
    <h1 class="person-name">Daniel Hartley</h1>
    <p class="person-title">Manager</p>
  </div>

  <div class="brand">
    <div class="brand-row">
      <span class="brand-mark"></span>
      <span class="brand-name">Oakridge Interiors</span>
    </div>
    <p class="brand-tagline">Trade Furniture Solutions</p>
  </div>

  <div class="divider"></div>

  <ul class="contacts">
    <li>
      <svg viewBox="0 0 16 16"><path d="M4 1l3 3-2 2c1 2 3 4 5 5l2-2 3 3-2 3C7 15 1 9 1 3z" fill="#0555a3"/></svg>
      020 7946 0312
    </li>
    <li>
      <svg viewBox="0 0 16 16"><rect x="4" y="1" width="8" height="14" rx="1.5" fill="none" stroke="#0555a3" stroke-width="1.6"/><circle cx="8" cy="12.5" r="1" fill="#0555a3"/></svg>
      020 7946 0000
    </li>
    <li>
      <svg viewBox="0 0 16 16"><rect x="1" y="3" width="14" height="10" fill="#0555a3"/><path d="M1 3l7 6 7-6" fill="none" stroke="#fff" stroke-width="1.2"/></svg>
      info@trade.oakridge.co.uk
    </li>
    <li>
      <svg viewBox="0 0 16 16"><circle cx="8" cy="8" r="7" fill="#0555a3"/><path d="M1 8h14M8 1c-3 3-3 11 0 14M8 1c3 3 3 11 0 14" fill="none" stroke="#fff" stroke-width="0.9"/></svg>
      www.trade.oakridge.co.uk
    </li>
  </ul>

  <address class="address" style="font-style:normal">
    27B Larkfield Trading Estate<br>
    Westbury Green, London
  </address>

  <svg class="edge-band" viewBox="0 0 700 30" preserveAspectRatio="none">
    <polygon points="0,6 330,18 345,30 0,30" fill="#85abd2"/>
    <polygon points="330,18 700,16 700,30 345,30" fill="#3176b5"/>
  </svg>
</section>

</body>
</html>
```